Business Card for Lantern Reach

Please design a Modern Business card for a Online Marketing Company

Website: http://www.lanternreach-example.com.au

Please do NOT include physical address in design.

```html
<!DOCTYPE html>
<html lang="en">
<head>
<meta charset="utf-8">
<title>Lantern Reach – Business Card</title>
<link rel="stylesheet" href="https://fonts.googleapis.com/css2?family=Roboto:wght@400;700;900&family=Open+Sans:wght@400;600;700&display=swap">
<style>
  :root {
    --brand-red: #c20016;
    --accent-orange: #f08a10;
    --ink: #1d1d1d;
    --paper: #ffffff;
    --stage: #ecebe8;
  }
  * { box-sizing: border-box; margin: 0; padding: 0; }
  html, body { width: 1200px; height: 483px; overflow: hidden; }
  body {
    background: var(--stage);
    font-family: "Roboto", Arial, sans-serif;
    display: flex;
    align-items: center;
    justify-content: center;
    gap: 70px;
  }
  .card {
    position: relative;
    width: 500px;
    height: 290px;
    overflow: hidden;
    box-shadow: 0 6px 18px rgba(0,0,0,0.18);
  }

  /* Front */
  .card--front { background: var(--paper); }
  .front__wave { position: absolute; inset: 0; width: 100%; height: 100%; }
  .brand {
    position: absolute;
    left: 48px;
    top: 40px;
    display: flex;
    align-items: center;
    gap: 14px;
  }
  .brand__square {
    width: 46px;
    height: 46px;
    background: var(--brand-red);
  }
  .brand__name {
    font-weight: 900;
    font-size: 27px;
    color: var(--brand-red);
    letter-spacing: 0.2px;
    line-height: 1;
  }
  .brand__tagline {
    font-weight: 700;
    font-size: 14px;
    color: var(--ink);
    margin-top: 3px;
  }
  .person {
    position: absolute;
    left: 140px;
    top: 126px;
    font-family: "Open Sans", Arial, sans-serif;
    color: var(--brand-red);
    font-size: 16px;
  }
  .person__name { font-weight: 700; font-size: 21px; letter-spacing: 0.8px; }
  .contact {
    position: absolute;
    right: 34px;
    top: 192px;
    list-style: none;
    font-family: "Open Sans", Arial, sans-serif;
    color: var(--paper);
    font-size: 14px;
    line-height: 1.55;
  }
  .contact li { display: flex; align-items: center; justify-content: flex-end; gap: 6px; }
  .contact svg { width: 12px; height: 12px; flex: none; }
  .icon--fill { fill: var(--paper); }
  .icon--line { fill: none; stroke: var(--paper); stroke-width: 2; }

  /* Back */
  .card--back {
    background: var(--brand-red);
    color: var(--paper);
    text-align: center;
  }
  .back__name {
    position: absolute;
    top: 92px;
    left: 0; right: 0;
    font-weight: 900;
    font-size: 44px;
    letter-spacing: 0.5px;
    line-height: 1;
  }
  .back__tagline {
    position: absolute;
    top: 140px;
    left: 0; right: 0;
    font-weight: 700;
    font-size: 21px;
  }
  .back__web {
    position: absolute;
    bottom: 42px;
    left: 0; right: 0;
    font-family: "Open Sans", Arial, sans-serif;
    font-size: 17px;
    letter-spacing: 0.4px;
  }
</style>
</head>
<body>

<section class="card card--front" aria-label="Business card front">
  <svg class="front__wave" viewBox="0 0 500 290" preserveAspectRatio="none" aria-hidden="true">
    <path d="M0,268 C120,180 300,140 500,162" fill="none" stroke="var(--accent-orange)" stroke-width="6"/>
    <path d="M0,280 C120,196 300,158 500,172 L500,290 L0,290 Z" fill="var(--brand-red)"/>
  </svg>

  <div class="brand">
    <div class="brand__square" aria-hidden="true"></div>
    <div>
      <div class="brand__name">LANTERN REACH</div>
      <div class="brand__tagline">Get seen online - Grow online</div>
    </div>
  </div>

  <p class="person"><span class="person__name">Your Name</span>, Title</p>

  <ul class="contact">
    <li>
      <svg class="icon--fill" viewBox="0 0 24 24" aria-hidden="true"><path d="M6.6 10.8a15 15 0 0 0 6.6 6.6l2.2-2.2a1 1 0 0 1 1-.25 11.4 11.4 0 0 0 3.6.57 1 1 0 0 1 1 1V20a1 1 0 0 1-1 1A17 17 0 0 1 3 4a1 1 0 0 1 1-1h3.5a1 1 0 0 1 1 1c0 1.25.2 2.45.57 3.6a1 1 0 0 1-.25 1z"/></svg>
      0400 123 456
    </li>
    <li>
      <svg class="icon--line" viewBox="0 0 24 24" aria-hidden="true"><rect x="2" y="5" width="20" height="14"/><path d="M2 5l10 8 10-8"/></svg>
      plan@lanternreach-example.com.au
    </li>
    <li>
      <svg class="icon--line" viewBox="0 0 24 24" aria-hidden="true"><circle cx="12" cy="12" r="10"/><path d="M2 12h20M12 2c3 3 3 17 0 20M12 2c-3 3-3 17 0 20"/></svg>
      www.lanternreach-example.com.au
    </li>
  </ul>
</section>

<section class="card card--back" aria-label="Business card back">
  <h1 class="back__name">LANTERN REACH</h1>
  <p class="back__tagline">Get seen online - Grow online</p>
  <p class="back__web">www.lanternreach-example.com.au</p>
</section>

</body>
</html>
```